Business Card Design for Technology Company

New business card design needed for technology company director.
Ideally, the design will fit the style and nature of the industry. We are a supplier of quality products and services, and we hope the design will give customers and suppliers this impression.

Target Market(s)

3D Printing Industry

Industry/Entity Type

Technology Equipment

Contact Information for Business Card

Name: Marcus Lin
Title: Director
Company address: Factory K4, 7B Harlowe Road, Springvale Victoria Australia 3150
Telephone: +61-3-8555 6413
Email: marcus.lin@vortalmake.com.au
Website: www.vortalmake.com.au

Requirements
Must have
• All information in business card details
• Company logo
• '3D Printers and 3D Print Filaments' at proper place
Nice to have
• Style to fit the industry
• Colour to fit logo

```html
<!DOCTYPE html>
<html lang="en">
<head>
<meta charset="utf-8">
<title>Vortal Make – Business Card</title>
<link href="https://fonts.googleapis.com/css2?family=Lato:wght@400&family=Michroma&display=swap" rel="stylesheet">
<style>
  :root {
    --backdrop: #2b2b2d;
    --card: #141415;
    --card-edge: #1c1c1e;
    --white: #f4f4f4;
    --muted: #c9c9c9;
    --blue: #1f6fb2;
    --orange: #f7a21b;
    --silver: #cfd2d5;
    --divider: #4a4a4c;
  }
  * { box-sizing: border-box; margin: 0; padding: 0; }
  html, body { width: 1200px; height: 900px; overflow: hidden; }
  body {
    background: var(--backdrop);
    font-family: "Lato", Arial, sans-serif;
    color: var(--white);
    position: relative;
  }
  .card {
    position: absolute;
    left: 320px;
    width: 560px;
    height: 342px;
    background: linear-gradient(160deg, var(--card-edge), var(--card) 60%);
    box-shadow: 0 10px 30px rgba(0,0,0,.45);
    overflow: hidden;
  }
  .card--front { top: 70px; }
  .card--back { top: 488px; }
  .brand-stripe {
    position: absolute; left: 0; right: 0; bottom: 0; height: 9px;
    background: linear-gradient(90deg,
      var(--blue) 0 36%, var(--orange) 36% 70%, var(--silver) 70% 100%);
  }
  .brand {
    position: absolute; left: 0; right: 0; top: 128px;
    display: flex; flex-direction: column; align-items: center; gap: 16px;
  }
  .brand__lockup { display: flex; align-items: center; gap: 18px; }
  .brand__mark { width: 46px; height: 46px; background: var(--orange); }
  .brand__name {
    font-family: "Michroma", Arial, sans-serif;
    font-size: 34px; letter-spacing: 4px; color: var(--white);
  }
  .tagline {
    font-size: 14px; letter-spacing: 2.5px; text-transform: uppercase;
    color: var(--muted);
  }
  .person {
    position: absolute; right: 278px; top: 128px; text-align: right;
  }
  .person__name {
    font-family: "Michroma", Arial, sans-serif;
    font-size: 17px; letter-spacing: 1px;
  }
  .person__title { font-size: 14px; color: var(--muted); margin-top: 4px; }
  .contact-divider {
    position: absolute; left: 300px; top: 118px; width: 1px; height: 82px;
    background: var(--divider);
  }
  .contact {
    position: absolute; left: 318px; top: 130px; list-style: none;
    font-size: 14px; line-height: 22px; color: var(--white);
  }
  .contact li { display: flex; align-items: center; gap: 7px; }
  .contact svg { width: 11px; height: 11px; flex: none; }
  .address {
    position: absolute; left: 30px; bottom: 34px;
    font-size: 16px; color: var(--muted);
  }
</style>
</head>
<body>
  <section class="card card--front" aria-label="Card front">
    <div class="brand">
      <div class="brand__lockup">
        <span class="brand__mark"></span>
        <span class="brand__name">VORTAL MAKE</span>
      </div>
      <p class="tagline">3D Printers and 3D Print Filaments</p>
    </div>
    <div class="brand-stripe"></div>
  </section>

  <section class="card card--back" aria-label="Card back">
    <div class="person">
      <div class="person__name">MARCUS LIN</div>
      <div class="person__title">Director</div>
    </div>
    <div class="contact-divider"></div>
    <ul class="contact">
      <li>
        <svg viewBox="0 0 12 12" aria-hidden="true"><path fill="#2d86d6" d="M2 4c0-2 1-3 3-3l1 2-1 1c.5 1.2 1.3 2 2.5 2.5l1-1 2 1c0 2-1 3-3 3C4.5 9.5 2 7 2 4z"/></svg>
        +61-3-8555 6413
      </li>
      <li>
        <svg viewBox="0 0 12 12" aria-hidden="true"><rect x="1" y="2.5" width="10" height="7" fill="#f7a21b"/><path d="M1 2.5l5 4 5-4" fill="none" stroke="#141415" stroke-width="1"/></svg>
        marcus.lin@vortalmake.com.au
      </li>
      <li>
        <svg viewBox="0 0 12 12" aria-hidden="true"><circle cx="6" cy="6" r="5" fill="#cfd2d5"/><path d="M1 6h10M6 1c-2 2.5-2 7.5 0 10M6 1c2 2.5 2 7.5 0 10" fill="none" stroke="#141415" stroke-width=".8"/></svg>
        www.vortalmake.com.au
      </li>
    </ul>
    <p class="address">Factory K4, 7B Harlowe Road, Springvale Victoria Australia 3150</p>
    <div class="brand-stripe"></div>
  </section>
</body>
</html>
```